Business card for Eyelash extension salon in Linden Vale,California USA

We need new business card for our salon in Linden Vale. The salon name is 'Lashvera' . We would like to have...Business name: Lashvera Name of person: will provide later Address 4720 N.Alder Crest Ave Linden Vale , LV 00412 Phone: will provide later (Text only) Web: www.lashverastudio.example Snapgrid icon, Circlebook icon follow us for seasonal campaign and news @lashverastudiolounge Design should look elegant, high-end, clean, simple, cohesive with my brand. Please refer my brand board. Business name color will be metallic bronzy color. Im thinking grey background or white background. Thanks

Target Market(s)

25-35. Gender neutral. People who are in Entertainment business industry.
This is High-end Eyelash extension salon in Linden Vale

Industry/Entity Type

Beauty Salon

Contact Information for Business Card

Business name: Lashvera
Name of person: will provide later
Address 4720 N.Alder Crest Ave Linden Vale , LV 00412
Phone: will provide later (Text only)
Web: www.lashverastudio.example
Snapgrid icon, Circlebook icon
follow us for seasonal campaign and news @lashverastudiolounge

Requirements
Must have
• Beautiful, elegant, clean and simple look but very attractive and modern
Should not have
• We don't like too clutter, too busy designs.

```html
<!DOCTYPE html>
<html lang="en">
<head>
<meta charset="utf-8">
<title>Lashvera Business Card</title>
<link rel="stylesheet" href="https://fonts.googleapis.com/css2?family=Playfair+Display:wght@700&family=Libre+Caslon+Text:wght@400;700&display=swap">
<style>
  :root {
    --bronze: #8a6547;
    --ink: #3a3a3a;
    --muted: #a8a8a8;
    --stage: #2b2b2b;
    --card-light: #fbfbfb;
    --card-grey: #d9d9d9;
    --marble-light: #f1f1f1;
    --marble-mid: #cfcfcf;
  }
  * { margin: 0; padding: 0; box-sizing: border-box; }
  html, body { width: 1200px; height: 960px; overflow: hidden; }
  body { background: var(--stage); position: relative; font-family: "Libre Caslon Text", Georgia, serif; }

  .card { position: absolute; width: 600px; height: 343px; box-shadow: 0 4px 10px rgba(0,0,0,.5); overflow: hidden; }
  .card-front { left: 302px; top: 122px;
    background: radial-gradient(ellipse 380px 260px at 440px 100px, #ffffff 0%, #f4f4f4 45%, transparent 75%),
                linear-gradient(115deg, var(--card-grey) 0%, #f2f2f2 40%, var(--card-light) 60%, #cfcfcf 100%); }
  .card-back { left: 299px; top: 495px; }

  .wordmark { position: absolute; color: var(--bronze); font-family: "Libre Caslon Text", Georgia, serif; font-weight: 400; white-space: nowrap; transform: translate(-50%, -50%); letter-spacing: .02em; }
  .card-front .wordmark { left: 168px; top: 170px; font-size: 46px; }

  .divider { position: absolute; left: 311px; top: 78px; width: 1px; height: 186px; background: linear-gradient(#e0e0e0, #9a9a9a, #e0e0e0); }

  .contact { position: absolute; left: 338px; top: 84px; color: var(--ink); font-size: 14.5px; line-height: 18px; }
  .contact-name { font-family: "Playfair Display", Georgia, serif; font-weight: 700; color: var(--bronze); font-size: 22px; line-height: 26px; letter-spacing: .01em; }
  .contact-title { font-weight: 700; color: var(--muted); font-size: 15px; line-height: 17px; margin-bottom: 11px; }
  .contact-address { margin-bottom: 12px; }
  .contact-line { display: flex; align-items: center; gap: 8px; height: 19px; }
  .contact-line svg { width: 13px; height: 13px; fill: var(--ink); flex: none; }

  .marble { position: absolute; inset: 0;
    background: radial-gradient(ellipse 300px 120px at 150px 270px, #bdbdbd 0%, transparent 70%),
                radial-gradient(ellipse 260px 100px at 470px 80px, #d2d2d2 0%, transparent 70%),
                linear-gradient(160deg, var(--marble-mid) 0%, var(--marble-light) 40%, #e6e6e6 70%, var(--marble-mid) 100%); }
  .card-back .wordmark { left: 301px; top: 158px; font-size: 74px; }
  .social { position: absolute; right: 34px; top: 38px; color: var(--bronze); font-size: 11px; font-weight: 700; letter-spacing: .04em; }
  .web-url { position: absolute; left: 0; right: 0; top: 288px; text-align: center; color: var(--bronze); font-family: "Playfair Display", Georgia, serif; font-weight: 700; font-size: 14px; letter-spacing: .3em; }
</style>
</head>
<body>
  <section class="card card-front">
    <div class="wordmark">Lashvera</div>
    <div class="divider"></div>
    <div class="contact">
      <div class="contact-name">MARA ELLISON</div>
      <div class="contact-title">CEO/FOUNDER</div>
      <div class="contact-address">4720 N.Alder Crest<br>Ave Linden Vale<br>LV 00412</div>
      <div class="contact-line">
        <svg viewBox="0 0 24 24" aria-hidden="true"><path d="M6.6 10.8a15 15 0 0 0 6.6 6.6l2.2-2.2c.3-.3.7-.4 1-.2 1.1.4 2.3.6 3.6.6.6 0 1 .4 1 1V20c0 .6-.4 1-1 1A17 17 0 0 1 3 4c0-.6.4-1 1-1h3.5c.6 0 1 .4 1 1 0 1.3.2 2.5.6 3.6.1.3 0 .7-.2 1z"/></svg>
        <span>310 555 0147</span>
      </div>
      <div class="contact-line">
        <svg viewBox="0 0 24 24" aria-hidden="true"><path d="M3 6v13h18V6l-9 7z M4 5h16l-8 6z"/></svg>
        <span>hello@lashverastudio.example</span>
      </div>
      <div class="contact-line">
        <svg viewBox="0 0 24 24" aria-hidden="true"><circle cx="12" cy="12" r="10"/><path d="M2 12h20M12 2c3 3 3 17 0 20M12 2c-3 3-3 17 0 20" fill="none" stroke="#fbfbfb" stroke-width="1.4"/></svg>
        <span>www.lashverastudio.example</span>
      </div>
    </div>
  </section>

  <section class="card card-back">
    <div class="marble" role="img" aria-label="White and grey marble texture background"></div>
    <div class="social">Circlebook · Snapgrid</div>
    <div class="wordmark">Lashvera</div>
    <div class="web-url">www.lashverastudio.example</div>
  </section>
</body>
</html>
```